ambitious event and festival agency from austria needs fresh business card design

A new design is due for the new headquarters and the new challenges. We organize events for different target groups from 16 to 60 years. The design should therefore be straightforward and not confused, so we are open to new colors and the logo may also be changed. In general, however, the most interesting suggestions are the most interesting ones. after this order we are looking for more graphics for brightloom facebook instagramm homepage etc A new design is due for the new headquarters and the new challenges. We organize events for different target groups from 16 to 60 years. The design should therefore be straightforward and not confused, so we are open to new colors and the logo may also be changed. In general, however, the most interesting suggestions are the most interesting ones. after this order we are looking for more graphics for brightloom facebook instagramm homepage etc A new design is due for the new headquarters and the new challenges. We organize events for different target groups from 16 to 60 years. The design should therefore be straightforward and not confused, so we are open to new colors and the logo may also be changed. In general, however, the most interesting suggestions are the most interesting ones. after this order we are looking for more graphics for brightloom facebook instagramm homepage etc
Updates

Reason: I am sorry for this decision but i need some more time. No new designs please, there are so many good ones and I will have made a decision in the next 3 days.

Target Market(s)

Industry/Entity Type

Business

Font styles to use
Serif
Sans Serif

Colors

Designer to choose colors to be used in the design.

Requirements
Must have
Nice to have
Should not have

```html
<!DOCTYPE html>
<html lang="en">
<head>
<meta charset="UTF-8">
<title>brightloom – business card</title>
<link rel="stylesheet" href="https://fonts.googleapis.com/css2?family=Oswald:wght@500&family=Work+Sans:wght@400;500&display=swap">
<style>
  :root {
    --backdrop: #1d1d1e;
    --card-grey: #6e7270;
    --card-white: #ffffff;
    --brand-red: #a3213a;
    --text-grey: #8a8d8c;
    --logo-white: #ffffff;
  }
  * { margin: 0; padding: 0; box-sizing: border-box; }
  html, body {
    width: 1200px;
    height: 900px;
    overflow: hidden;
    background: var(--backdrop);
  }
  .canvas {
    position: relative;
    width: 1200px;
    height: 900px;
  }
  .card {
    position: absolute;
    top: 295px;
    width: 540px;
    height: 310px;
    border-radius: 22px;
    overflow: hidden;
  }
  .card--front {
    left: 40px;
    background: var(--card-grey);
    display: flex;
    align-items: center;
    justify-content: center;
  }
  .card--back {
    left: 620px;
    background: var(--card-white);
  }
  .wordmark {
    font-family: "Work Sans", sans-serif;
    font-weight: 500;
    letter-spacing: -0.5px;
    line-height: 1;
  }
  .card--front .wordmark {
    color: var(--logo-white);
    font-size: 64px;
  }
  .card--back .wordmark {
    position: absolute;
    top: 36px;
    right: 28px;
    color: var(--brand-red);
    font-size: 44px;
  }
  .contact {
    position: absolute;
    top: 118px;
    right: 290px;
    text-align: right;
    font-family: "Work Sans", sans-serif;
    font-size: 13px;
    line-height: 1.32;
    color: var(--text-grey);
    white-space: nowrap;
  }
  .contact__name {
    font-family: "Oswald", sans-serif;
    font-weight: 500;
    font-size: 20px;
    letter-spacing: 0.5px;
    text-transform: uppercase;
    color: var(--brand-red);
    line-height: 1.15;
  }
  .contact__role { margin-bottom: 10px; }
  .contact__address { margin-bottom: 6px; }
  .contact__line {
    display: flex;
    justify-content: flex-end;
    align-items: center;
    gap: 10px;
  }
  .contact__line svg {
    width: 11px;
    height: 11px;
    flex: none;
  }
  .contact__accent { color: var(--brand-red); }
</style>
</head>
<body>
  <main class="canvas">
    <section class="card card--front" aria-label="Card front">
      <div class="wordmark">brightloom</div>
    </section>

    <section class="card card--back" aria-label="Card back">
      <div class="wordmark">brightloom</div>

      <div class="contact">
        <div class="contact__name">Markus Feldinger</div>
        <div class="contact__role">Manager</div>
        <div class="contact__address">
          brightloom<br>
          Lindenweg 12<br>
          A4820 Talheim
        </div>
        <div class="contact__line">
          <span>+ 43 660 418 372 5</span>
          <svg viewBox="0 0 12 12" aria-hidden="true"><rect x="3" y="1" width="6" height="10" rx="1" fill="none" stroke="var(--brand-red)" stroke-width="1.2"/><circle cx="6" cy="9" r="0.7" fill="var(--brand-red)"/></svg>
        </div>
        <div class="contact__line">
          <span>m.feldinger@brightloom.eu</span>
          <svg viewBox="0 0 12 12" aria-hidden="true"><rect x="1" y="3" width="10" height="7" fill="none" stroke="var(--brand-red)" stroke-width="1.2"/><path d="M1 3 L6 7 L11 3" fill="none" stroke="var(--brand-red)" stroke-width="1.2"/></svg>
        </div>
        <div class="contact__line">
          <span>www.<span class="contact__accent">brightloom</span>.eu</span>
          <svg viewBox="0 0 12 12" aria-hidden="true"><circle cx="6" cy="6" r="5" fill="none" stroke="var(--brand-red)" stroke-width="1.1"/><ellipse cx="6" cy="6" rx="2.2" ry="5" fill="none" stroke="var(--brand-red)" stroke-width="1"/><path d="M1 6 H11 M2 3.5 H10 M2 8.5 H10" stroke="var(--brand-red)" stroke-width="0.9"/></svg>
        </div>
      </div>
    </section>
  </main>
</body>
</html>
```